New, modern business card for growing audiology practice

We need a new business card for our audiology practice. Our logo and website have recently changed (more modern) and we want our business cards to reflect this change.
We conduct hearing tests, perform earwax removals, and fit & dispense hearing aids to our patients. We are a family owned practice in which the owner is the one who works directly with the patient. I have attached logos in various formats to use, as well as two ideas I found on this website; as well as a scanned copy of our current logo. Good luck!

Industry/Entity Type

Business

Contact Information for Business Card

Company name: Tolvera Hearing Center
Provider name: Peter Wolstenby, Au.D. F/NSB
Phone number: (440) 683-5127
Address: 837 W. Lindell Ave. Marbrook Falls, OH 40517
email: tolverahearing@postvane.com
website: tolverahearing.com

Colors
000000
aaaaaa
dbdbdb
cacaca
9bcb3c
afd23c
cadf82
b1b1b1

Requirements
Must have
• My card must include information in the "details" section. In the attached images, I found a few that I liked and I would like to model after - "brisky bouncin'" and "Sound Method Center".
• Must be horizontal.
• Must include logos provided. I uploaded them in various file formats and various ways.
• Must match logo font, if possible, if not, please get as close as you can.
Nice to have
• I really like the idea of having a color on one side with just the logo and company name and the contact information and provider name on the other side. I also really like the idea of having the main color dominating on the logo/company side with accent of that same color on the contact side of the card.
Should not have
• Must not be vertical.

```html
<!DOCTYPE html>
<html lang="en">
<head>
<meta charset="utf-8">
<title>Tolvera Hearing Center — Business Card</title>
<link rel="stylesheet" href="https://fonts.googleapis.com/css2?family=Open+Sans:wght@400;600;700&display=swap">
<style>
  :root {
    --backdrop: #e4e4e4;
    --card-black: #111111;
    --card-black-edge: #1c1c1c;
    --card-white: #ffffff;
    --ink: #1a1a1a;
    --grey: #6b6b6b;
    --green: #9bcb3c;
    --green-deep: #7aa83a;
    --light-text: #f2f2f2;
  }
  * { box-sizing: border-box; margin: 0; padding: 0; }
  html, body {
    width: 1200px; height: 873px; overflow: hidden;
    background: var(--backdrop);
    font-family: "Open Sans", Arial, sans-serif;
  }
  .canvas {
    position: relative; width: 1200px; height: 873px;
    display: flex; align-items: center; justify-content: center; gap: 40px;
  }
  .card {
    width: 540px; height: 309px; position: relative;
    box-shadow: 0 6px 18px rgba(0,0,0,0.18);
  }
  .card--back {
    background: radial-gradient(ellipse at 50% 40%, var(--card-black-edge), var(--card-black));
    display: flex; align-items: center; justify-content: center;
  }
  .brand { display: flex; align-items: center; gap: 8px; }
  .brand__dot {
    width: 12px; height: 12px; border-radius: 50%; background: var(--green);
  }
  .brand__name {
    font-weight: 600; font-size: 20px; letter-spacing: 0.5px;
    text-transform: uppercase; color: var(--light-text);
  }
  .back__url {
    position: absolute; bottom: 22px; left: 0; right: 0; text-align: center;
    font-size: 12px; font-weight: 600; color: var(--light-text);
  }
  .back__url .accent { color: var(--green); }
  .card--front { background: var(--card-white); padding: 28px 28px; }
  .front__brand {
    font-weight: 600; font-size: 18px; text-transform: uppercase;
    color: var(--ink); letter-spacing: 0.3px;
  }
  .provider { margin-top: 80px; }
  .provider__name {
    font-weight: 700; font-size: 12.5px; color: var(--green-deep); text-transform: uppercase;
  }
  .provider__role { font-size: 11px; color: var(--grey); }
  .address { margin-top: 14px; font-size: 11.5px; color: var(--grey); line-height: 1.45; }
  .contacts { margin-top: 14px; list-style: none; font-size: 11.5px; color: var(--grey); line-height: 1.55; }
  .contacts li { display: flex; align-items: center; gap: 8px; }
  .contacts svg { width: 10px; height: 10px; flex: none; fill: none; stroke: var(--green-deep); stroke-width: 2; }
  .contacts .accent { color: var(--green-deep); }
</style>
</head>
<body>
<main class="canvas">
  <section class="card card--back" aria-label="Card back">
    <div class="brand">
      <span class="brand__dot"></span>
      <span class="brand__name">Tolvera Hearing Center</span>
    </div>
    <p class="back__url">www.<span class="accent">tolverahearing</span>.com</p>
  </section>

  <section class="card card--front" aria-label="Card front">
    <h1 class="front__brand">Tolvera Hearing Center</h1>
    <div class="provider">
      <p class="provider__name">Peter Wolstenby, Au.D. F/NSB</p>
      <p class="provider__role">Owner-Audiologist</p>
    </div>
    <p class="address">837 W. Lindell Ave.<br>Marbrook Falls, OH 40517</p>
    <ul class="contacts">
      <li><svg viewBox="0 0 10 10"><path d="M2 1 L4 1 L4.5 3 L3.3 4 Q4.5 6 6 6.7 L7 5.5 L9 6 L9 8 Q5 9 1.5 4.5 Q1 2.5 2 1Z"/></svg><span>(440) 683-5127</span></li>
      <li><svg viewBox="0 0 10 10"><rect x="1" y="2" width="8" height="6"/><path d="M1 2 L5 5.5 L9 2"/></svg><span>tolverahearing@postvane.com</span></li>
      <li><svg viewBox="0 0 10 10"><circle cx="5" cy="5" r="4"/><path d="M1 5 H9 M5 1 Q2.5 5 5 9 M5 1 Q7.5 5 5 9"/></svg><span>www.<span class="accent">tolverahearing</span>.com</span></li>
    </ul>
  </section>
</main>
</body>
</html>
```